Velk Partners Building Business Cards

We need a business card that reflects our business as "Solar Experts" in San Diego. Browse our website www.velkpartners.example our License needs to be displayed as "CSLB# 3867140" our phone number is (619) 555-0187

Save thousands on your electric bills and increase the value of your home while helping to protect the environment. Our solar installation experts will help you design the system that's right for you, using only the highest quality equipment that will look great and give you ideal performance. Our goal is to make you energy independent, and get your electric bill to 0.

Paul Osterby
(619) 555-0187
paul@velkpartners.example

Target Market(s)

Home owners in san diego looking for solar

Industry/Entity Type

Solar Energy

Contact Information for Business Card

Paul Osterby
(619) 555-0187
paul@velkpartners.example

Font styles to use
Other font styles liked:
• Use our logo font

Requirements
Must have
• License needs to be displayed as "CSLB# 3867140" our phone number is (619) 555-0187
Nice to have
• Real images of rooftop home solar in san diego
Should not have
• our business address

```html
<!DOCTYPE html>
<html lang="en">
<head>
<meta charset="utf-8">
<title>Velk Partners Building – Business Cards</title>
<link rel="stylesheet" href="https://fonts.googleapis.com/css2?family=Open+Sans:wght@400;600;700&display=swap">
<style>
  :root {
    --navy: #1b3c72;
    --gold: #f5ae0a;
    --gold-soft: #fde7b3;
    --ink: #4a4a4a;
    --paper: #ffffff;
    --backdrop: #2b2b2b;
    --card-w: 615px;
    --card-h: 352px;
  }
  * { box-sizing: border-box; margin: 0; padding: 0; }
  html, body {
    width: 1200px;
    height: 987px;
    overflow: hidden;
    background: var(--backdrop);
    font-family: "Open Sans", Arial, sans-serif;
  }
  .sheet {
    position: relative;
    width: 1200px;
    height: 987px;
  }
  .card {
    position: absolute;
    left: 292px;
    width: var(--card-w);
    height: var(--card-h);
    overflow: hidden;
  }
  .card--front { top: 130px; background: var(--paper); }
  .card--back  { top: 505px; background: var(--navy); }

  .wordmark {
    display: flex;
    align-items: center;
    gap: 10px;
    font-weight: 700;
    letter-spacing: -0.5px;
    white-space: nowrap;
  }
  .wordmark__dot {
    width: 22px;
    height: 22px;
    border-radius: 50%;
    background: var(--gold);
    flex: none;
  }
  .card--front .wordmark {
    position: absolute;
    left: 34px;
    top: 44px;
    font-size: 31px;
    color: var(--navy);
  }

  .emblem-area {
    position: absolute;
    right: 0;
    bottom: 0;
    width: 360px;
    height: 270px;
    background: radial-gradient(ellipse at 85% 95%, var(--gold-soft) 0%, rgba(253,231,179,0.35) 45%, rgba(255,255,255,0) 72%);
  }

  .holder {
    position: absolute;
    left: 34px;
    top: 144px;
  }
  .holder__name {
    font-size: 21px;
    font-weight: 600;
    color: var(--navy);
    line-height: 1.2;
  }
  .holder__role {
    font-size: 15px;
    color: var(--gold);
    line-height: 1.3;
  }
  .holder__licence {
    margin-top: 14px;
    font-size: 15px;
    color: var(--ink);
  }
  .contacts {
    list-style: none;
    margin-top: 16px;
  }
  .contacts li {
    display: flex;
    align-items: center;
    gap: 8px;
    font-size: 15px;
    color: var(--ink);
    line-height: 24px;
  }
  .contacts svg { width: 15px; height: 15px; fill: var(--navy); flex: none; }

  .card--back .wordmark {
    position: absolute;
    left: 0;
    right: 0;
    top: 136px;
    justify-content: center;
    font-size: 38px;
    color: var(--paper);
  }
  .card--back .wordmark__dot { width: 26px; height: 26px; }
  .site {
    position: absolute;
    left: 0;
    right: 0;
    top: 292px;
    text-align: center;
    font-size: 15px;
    letter-spacing: 0.36em;
    color: var(--paper);
  }
</style>
</head>
<body>
<main class="sheet">
  <section class="card card--front" aria-label="Business card front">
    <div class="wordmark"><span class="wordmark__dot"></span>Velk Partners Building</div>
    <div class="emblem-area" role="img" aria-label="Space for the company sun-over-wave emblem"></div>
    <div class="holder">
      <p class="holder__name">Paul Osterby</p>
      <p class="holder__role">CEO/Founder</p>
      <p class="holder__licence">CSLB# 3867140</p>
      <ul class="contacts">
        <li>
          <svg viewBox="0 0 16 16" aria-hidden="true"><path d="M3.6 1.2l2.3 2.4-1.4 2a9 9 0 0 0 5.9 5.9l2-1.4 2.4 2.3-1.6 2.3C7 14.6 1.4 9 .7 2.8z"/></svg>
          (619) 555-0187
        </li>
        <li>
          <svg viewBox="0 0 16 16" aria-hidden="true"><path d="M1 3h14v1.2L8 9 1 4.2zM1 5.8l7 4.7 7-4.7V13H1z"/></svg>
          paul@velkpartners.example
        </li>
        <li>
          <svg viewBox="0 0 16 16" aria-hidden="true"><path d="M8 1a7 7 0 1 0 0 14A7 7 0 0 0 8 1zm0 1.6c.9.8 1.6 2.2 1.8 3.9H6.2C6.4 4.8 7.1 3.4 8 2.6zM6.2 8h3.6c-.2 1.7-.9 3.1-1.8 3.9-.9-.8-1.6-2.2-1.8-3.9zM2.6 8h2.1c.1 1.4.5 2.7 1.1 3.7A5.5 5.5 0 0 1 2.6 8zm8.7 0h2.1a5.5 5.5 0 0 1-3.2 3.7c.6-1 1-2.3 1.1-3.7zM2.6 6.5a5.5 5.5 0 0 1 3.2-3.7c-.6 1-1 2.3-1.1 3.7zm8.7 0c-.1-1.4-.5-2.7-1.1-3.7a5.5 5.5 0 0 1 3.2 3.7z"/></svg>
          www.velkpartners.example
        </li>
      </ul>
    </div>
  </section>

  <section class="card card--back" aria-label="Business card back">
    <div class="wordmark"><span class="wordmark__dot"></span>Velk Partners Building</div>
    <p class="site">www.velkpartners.example</p>
  </section>
</main>
</body>
</html>
```